Business Intelligence / Data Visualization Firm Seeking World Class Power Point Deck

Vela Crest delivers enterprise business intelligence and data visualization solutions enabling clients to see their business as they've never seen it - we transform complex, unstructured data into simple insight that facilitates intelligent decision making, revenue growth and risk reduction. We're seeking a world class power point template for internal, client and conference presentations.

Please visit velacrest.example for more company context.
*Note: A website photo has been uploaded and may be used or not used - designer discretion.

Additional context:
We use Lumadrift: https://lumadrift.norvex.example/products/predictive-analytics.

Target Market(s)

CXOs at Meridian 100 companies | small and medium business owners (BI / data-viz experts and also decision makers who don't actually understand BI / data-viz).

Industry/Entity Type

Professional Service

Font styles to use
Sans Serif
Other font styles liked:
• Our logo is Expansiva (uploaded), our site is Tahoma. Please use your discretion,.

Colors
ec1f27
ffffff
000000

Requirements
Must have
• PPT format, editable.
• Prefer simple, clean, strong presentation.
Nice to have
• Designs that relate to data, analytics, solutions, automation and transforming complexity into simplicity.
• Reusable icons.

```html
<!DOCTYPE html>
<html lang="en">
<head>
<meta charset="utf-8">
<title>Vela Crest – Individual Slides</title>
<link rel="stylesheet" href="https://fonts.googleapis.com/css2?family=Michroma&family=Open+Sans:ital,wght@0,400;0,600;1,400&family=Roboto+Slab:wght@800&display=swap">
<style>
  :root{
    --red:#ec1f27;
    --black:#000000;
    --white:#ffffff;
    --ink:#1b1b1b;
    --grey:#9a9a9a;
    --grey-light:#c9c9c9;
    --grey-dark:#555555;
    --page:#f3f1ee;
    --heading:#5a5a5a;
  }
  html,body{margin:0;padding:0;}
  body{
    width:1200px;height:1200px;overflow:hidden;
    background:var(--page);
    font-family:"Open Sans",sans-serif;
  }
  .sheet-title{
    margin:0;padding-top:12px;height:40px;
    text-align:center;
    font-family:"Roboto Slab",serif;font-weight:800;
    font-size:24px;color:var(--heading);letter-spacing:.5px;
  }
  .slide-grid{
    position:absolute;left:138px;top:80px;
    display:grid;
    grid-template-columns:repeat(3,284px);
    grid-auto-rows:162px;
    column-gap:48px;row-gap:24px;
  }
  .slide{
    width:284px;height:162px;display:block;
    box-shadow:0 3px 8px rgba(0,0,0,.22);
    background:var(--white);
  }
  .slide-title{font-family:"Michroma",sans-serif;font-size:8.5px;fill:var(--ink);letter-spacing:.6px;}
  .slide-sub{font-size:3px;fill:var(--grey);}
  .body-copy{font-size:3.3px;font-style:italic;fill:#666;}
  .label{font-size:3.6px;fill:#333;font-weight:600;}
  .small{font-size:3px;fill:#777;}
  .axis{font-size:3.4px;fill:#666;}
  .grid line{stroke:#e4e4e4;stroke-width:.6;}
  .brand{font-family:"Michroma",sans-serif;fill:var(--white);font-size:6.4px;letter-spacing:.4px;}
  .footer-url{font-family:"Michroma",sans-serif;font-size:3.4px;fill:var(--white);letter-spacing:1px;}
  .big-num{font-family:"Open Sans",sans-serif;font-size:9px;fill:var(--red);}
</style>
</head>
<body>

<h1 class="sheet-title">01 b - Individual Slides</h1>

<svg width="0" height="0" style="position:absolute" aria-hidden="true">
  <defs>
    <symbol id="slide-chrome" viewBox="0 0 355 203">
      <rect width="355" height="203" fill="#fbfbfb"/>
      <path d="M4 5 H10 M4 5 V12" stroke="var(--red)" stroke-width="1.6" fill="none"/>
      <rect x="274" y="5" width="76" height="13" fill="var(--black)"/>
      <text class="brand" x="312" y="13.6" text-anchor="middle">VELA CREST</text>
      <rect x="0" y="196" width="355" height="7" fill="var(--black)"/>
      <text class="footer-url" x="10" y="201">WWW.VELACREST.EXAMPLE</text>
      <text class="footer-url" x="345" y="201" text-anchor="end">24</text>
    </symbol>
    <symbol id="intro-copy" viewBox="0 0 355 203">
      <text class="body-copy" x="22" y="42">Clear insight starts with simple data. This slide shows how each figure compares over time and why it matters for planning.</text>
      <text class="body-copy" x="22" y="48">Replace this sample text with a short summary of the chart and the key decision it should support.</text>
    </symbol>
  </defs>
</svg>

<main class="slide-grid">

  <!-- 1 Title slide -->
  <svg class="slide" viewBox="0 0 355 203" preserveAspectRatio="none">
    <use href="#slide-chrome" width="355" height="203"/>
    <rect x="0" y="0" width="142" height="196" fill="#3c4657" role="img" aria-label="Office desk photo with charts, tinted dark slate"/>
    <text class="slide-title" x="9" y="17" fill="#fff" style="fill:#fff">TITLE HERE</text>
    <text class="slide-sub" x="9" y="23" style="fill:#cfd5de">Enter your subtitle here</text>
    <g class="body-copy" style="fill:#dfe3ea">
      <text x="12" y="48">Sample text for the opening slide goes here,</text>
      <text x="12" y="55">it gives a short line about the firm and how</text>
      <text x="12" y="62">data turns into simple and useful insight.</text>
      <text x="12" y="69">Keep it brief and focused on outcomes.</text>
      <text x="12" y="90">Our team builds dashboards that help leaders</text>
      <text x="12" y="97">see trends early, reduce risk and grow</text>
      <text x="12" y="104">revenue with confidence every quarter.</text>
      <text x="12" y="111">Edit this copy to suit each presentation.</text>
    </g>
    <g>
      <path d="M143 112 L143 37 A75 75 0 0 1 196 59 Z" fill="#e03a4e"/>
      <path d="M143 112 L196 59 A75 75 0 0 1 218 112 Z" fill="#2b5a78"/>
      <path d="M143 112 L218 112 A75 75 0 0 1 196 165 Z" fill="#3aa6a6"/>
      <path d="M143 112 L196 165 A75 75 0 0 1 143 187 Z" fill="#f2c12e"/>
      <circle cx="143" cy="112" r="28" fill="#fff"/>
      <text x="143" y="113" text-anchor="middle" style="font-family:Michroma,sans-serif;font-size:3.4px;fill:#222">VELA CREST</text>
    </g>
    <g>
      <text class="label" x="228" y="42">Your Title Here</text>
      <text class="small" x="228" y="48">Short line of supporting text</text>
      <text class="label" x="250" y="80">Your Title Here</text>
      <text class="small" x="250" y="86">Short line of supporting text</text>
      <text class="label" x="250" y="128">Your Title Here</text>
      <text class="small" x="250" y="134">Short line of supporting text</text>
      <text class="label" x="228" y="170">Your Title Here</text>
      <text class="small" x="228" y="176">Short line of supporting text</text>
    </g>
  </svg>

  <!-- 2 Your title here -->
  <svg class="slide" viewBox="0 0 355 203" preserveAspectRatio="none">
    <use href="#slide-chrome" width="355" height="203"/>
    <text class="slide-title" x="9" y="17">YOUR TITLE HERE</text>
    <text class="slide-sub" x="9" y="23">Enter your subtitle here</text>
    <use href="#intro-copy" width="355" height="203"/>
    <g fill="none" stroke-width="6">
      <circle cx="50" cy="126" r="24" stroke="var(--red)"/>
      <circle cx="106" cy="126" r="24" stroke="var(--black)"/>
      <circle cx="162" cy="126" r="24" stroke="var(--red)"/>
      <circle cx="218" cy="126" r="24" stroke="var(--black)"/>
    </g>
    <circle cx="50" cy="126" r="16" fill="var(--red)" stroke="#fff" stroke-width="1.5"/>
    <circle cx="106" cy="126" r="16" fill="var(--black)" stroke="#fff" stroke-width="1.5"/>
    <circle cx="162" cy="126" r="16" fill="var(--red)" stroke="#fff" stroke-width="1.5"/>
    <circle cx="218" cy="126" r="16" fill="var(--black)" stroke="#fff" stroke-width="1.5"/>
    <g fill="none" stroke="#fff" stroke-width="1.2">
      <rect x="45" y="121" width="10" height="10"/>
      <circle cx="106" cy="126" r="5"/>
      <rect x="157" y="122" width="10" height="8"/>
      <rect x="213" y="121" width="10" height="9"/>
    </g>
    <text class="label" x="106" y="84" text-anchor="middle">Titles Goes Here</text>
    <text class="small" x="106" y="90" text-anchor="middle">Suitable for all categories</text>
    <text class="label" x="218" y="84" text-anchor="middle">Titles Goes Here</text>
    <text class="small" x="218" y="90" text-anchor="middle">Suitable for all categories</text>
    <text class="label" x="50" y="162" text-anchor="middle">Titles Goes Here</text>
    <text class="small" x="50" y="168" text-anchor="middle">Suitable for all categories</text>
    <text class="label" x="162" y="162" text-anchor="middle">Titles Goes Here</text>
    <text class="small" x="162" y="168" text-anchor="middle">Suitable for all categories</text>
    <text x="300" y="128" text-anchor="middle" style="font-family:Michroma,sans-serif;font-size:7px;fill:#111">VELA CREST</text>
  </svg>

  <!-- 3 Pie chart -->
  <svg class="slide" viewBox="0 0 355 203" preserveAspectRatio="none">
    <use href="#slide-chrome" width="355" height="203"/>
    <text class="slide-title" x="9" y="17">PIE CHART</text>
    <text class="slide-sub" x="9" y="23">Enter your subtitle here</text>
    <use href="#intro-copy" width="355" height="203"/>
    <g>
      <path d="M160 118 L130 112 A70 20 0 0 1 95 125 L95 137 A70 20 0 0 0 130 124 Z" fill="#555"/>
      <path d="M160 110 L100 116 A70 20 0 0 1 140 100 Z" fill="#6b6b6b"/>
      <path d="M160 110 L140 100 A70 20 0 0 1 175 98 Z" fill="#9a9a9a"/>
      <path d="M156 122 L100 126 A70 20 0 0 0 156 142 Z" fill="#d6d6d6"/>
      <path d="M156 142 L100 126 L100 136 A70 20 0 0 0 156 152 Z" fill="#aaa"/>
      <path d="M170 112 L180 98 A70 22 0 0 1 232 124 A70 22 0 0 1 165 134 Z" fill="var(--red)"/>
      <path d="M165 134 A70 22 0 0 0 232 124 L232 136 A70 22 0 0 1 165 146 Z" fill="#b5141b"/>
    </g>
    <g>
      <text class="label" x="30" y="76">Enter Your Title Here</text>
      <text class="small" x="30" y="82">Short supporting text line</text>
      <text class="label" x="254" y="76">Enter Your Title Here</text>
      <text class="small" x="254" y="82">Short supporting text line</text>
      <text class="label" x="40" y="165">Enter Your Title Here</text>
      <text class="small" x="40" y="171">Short supporting text line</text>
      <text class="label" x="264" y="162">Enter Your Title Here</text>
      <text class="small" x="264" y="168">Short supporting text line</text>
    </g>
    <g stroke="#999" stroke-width=".5" stroke-dasharray="1.5 1.5" fill="none">
      <path d="M90 78 L118 100"/><path d="M250 78 L222 108"/>
      <path d="M105 162 L120 140"/><path d="M260 160 L220 140"/>
    </g>
  </svg>

  <!-- 4 Column chart comparison -->
  <svg class="slide" viewBox="0 0 355 203" preserveAspectRatio="none">
    <use href="#slide-chrome" width="355" height="203"/>
    <text class="slide-title" x="9" y="17">COLUMN CHART COMPARISION</text>
    <text class="slide-sub" x="9" y="23">Enter your subtitle here</text>
    <use href="#intro-copy" width="355" height="203"/>
    <g class="grid"><line x1="22" x2="330" y1="65" y2="65"/><line x1="22" x2="330" y1="85" y2="85"/><line x1="22" x2="330" y1="105" y2="105"/><line x1="22" x2="330" y1="125" y2="125"/><line x1="22" x2="330" y1="145" y2="145"/></g>
    <g>
      <rect x="48" y="75" width="17" height="79" fill="var(--red)"/><rect x="71" y="109" width="17" height="45" fill="#000"/><rect x="94" y="116" width="17" height="38" fill="var(--grey)"/>
      <rect x="146" y="75" width="17" height="79" fill="var(--red)"/><rect x="169" y="109" width="17" height="45" fill="#000"/><rect x="192" y="116" width="17" height="38" fill="var(--grey)"/>
      <rect x="244" y="75" width="17" height="79" fill="var(--red)"/><rect x="267" y="109" width="17" height="45" fill="#000"/><rect x="290" y="116" width="17" height="38" fill="var(--grey)"/>
    </g>
    <g class="small">
      <circle cx="50" cy="167" r="1.3" fill="var(--red)"/><text x="53" y="168">Element</text>
      <circle cx="72" cy="167" r="1.3" fill="#000"/><text x="75" y="168">Element</text>
      <circle cx="94" cy="167" r="1.3" fill="var(--grey)"/><text x="97" y="168">Element</text>
      <circle cx="148" cy="167" r="1.3" fill="#f2c12e"/><text x="151" y="168">Element</text>
      <circle cx="170" cy="167" r="1.3" fill="#000"/><text x="173" y="168">Element</text>
      <circle cx="192" cy="167" r="1.3" fill="var(--grey)"/><text x="195" y="168">Element</text>
      <circle cx="246" cy="167" r="1.3" fill="var(--red)"/><text x="249" y="168">Element</text>
      <circle cx="268" cy="167" r="1.3" fill="#000"/><text x="271" y="168">Element</text>
      <circle cx="290" cy="167" r="1.3" fill="var(--grey)"/><text x="293" y="168">Element</text>
    </g>
  </svg>

  <!-- 5 Column chart with pie -->
  <svg class="slide" viewBox="0 0 355 203" preserveAspectRatio="none">
    <use href="#slide-chrome" width="355" height="203"/>
    <text class="slide-title" x="9" y="17">COLUMN CHART WITH PIE CHART</text>
    <text class="slide-sub" x="9" y="23">Enter your subtitle here</text>
    <use href="#intro-copy" width="355" height="203"/>
    <g>
      <rect x="52" y="126" width="20" height="22" fill="#000"/>
      <rect x="78" y="116" width="20" height="32" fill="#666"/>
      <rect x="104" y="82" width="20" height="66" fill="var(--grey)"/>
      <rect x="130" y="70" width="20" height="78" fill="var(--red)"/>
    </g>
    <circle cx="256" cy="106" r="33" fill="none" stroke="#000" stroke-width="7"/>
    <circle cx="256" cy="106" r="33" fill="none" stroke="var(--red)" stroke-width="7" pathLength="100" stroke-dasharray="22 100" transform="rotate(-90 256 106)"/>
    <text x="256" y="105" text-anchor="middle" style="font-size:11px;fill:#111">50bn</text>
    <text class="small" x="256" y="113" text-anchor="middle">Short note here</text>
    <g>
      <circle cx="32" cy="172" r="1.6" fill="#000"/><text class="label" x="40" y="166">Enter Your Title Here</text><text class="small" x="40" y="172">Short text line here</text>
      <circle cx="112" cy="172" r="1.6" fill="#888"/><text class="label" x="120" y="166">Enter Your Title Here</text><text class="small" x="120" y="172">Short text line here</text>
      <circle cx="192" cy="172" r="1.6" fill="#bbb"/><text class="label" x="200" y="166">Enter Your Title Here</text><text class="small" x="200" y="172">Short text line here</text>
      <circle cx="268" cy="172" r="1.6" fill="var(--red)"/><text class="label" x="276" y="166">Enter Your Title Here</text><text class="small" x="276" y="172">Short text line here</text>
    </g>
  </svg>

  <!-- 6 Column chart -->
  <svg class="slide" viewBox="0 0 355 203" preserveAspectRatio="none">
    <use href="#slide-chrome" width="355" height="203"/>
    <text class="slide-title" x="9" y="17">COLUMN CHART</text>
    <text class="slide-sub" x="9" y="23">Enter your subtitle here</text>
    <use href="#intro-copy" width="355" height="203"/>
    <g>
      <circle cx="40" cy="88" r="8" fill="var(--red)"/><rect x="37" y="85" width="6" height="6" fill="none" stroke="#fff" stroke-width=".8"/>
      <text class="label" x="56" y="84">Your Title Here</text><text class="small" x="56" y="90">Short line of supporting text</text>
      <circle cx="40" cy="120" r="8" fill="#888"/><circle cx="40" cy="120" r="3" fill="none" stroke="#fff" stroke-width=".8"/>
      <text class="label" x="56" y="116">Your Title Here</text><text class="small" x="56" y="122">Short line of supporting text</text>
      <circle cx="40" cy="152" r="8" fill="#111"/><rect x="36.5" y="149" width="7" height="5" fill="none" stroke="#fff" stroke-width=".8"/>
      <text class="label" x="56" y="148">Your Title Here</text><text class="small" x="56" y="154">Short line of supporting text</text>
    </g>
    <g class="axis" text-anchor="end">
      <text x="160" y="73">6</text><text x="160" y="89">5</text><text x="160" y="105">4</text><text x="160" y="121">3</text><text x="160" y="137">2</text><text x="160" y="153">1</text><text x="160" y="169">0</text>
    </g>
    <g>
      <rect x="174" y="100" width="5" height="68" fill="var(--red)"/><rect x="180" y="130" width="5" height="38" fill="#aaa"/><rect x="186" y="140" width="5" height="28" fill="#444"/>
      <rect x="209" y="110" width="5" height="58" fill="var(--red)"/><rect x="215" y="120" width="5" height="48" fill="#aaa"/><rect x="221" y="136" width="5" height="32" fill="#444"/>
      <rect x="244" y="116" width="5" height="52" fill="var(--red)"/><rect x="250" y="124" width="5" height="44" fill="#aaa"/><rect x="256" y="112" width="5" height="56" fill="#444"/>
      <rect x="279" y="98" width="5" height="70" fill="var(--red)"/><rect x="285" y="110" width="5" height="58" fill="#aaa"/><rect x="291" y="92" width="5" height="76" fill="#444"/>
    </g>
    <g class="axis" text-anchor="middle"><text x="183" y="176">2002</text><text x="218" y="176">2005</text><text x="253" y="176">2010</text><text x="288" y="176">2015</text></g>
  </svg>

  <!-- 7 3D data column chart -->
  <svg class="slide" viewBox="0 0 355 203" preserveAspectRatio="none">
    <use href="#slide-chrome" width="355" height="203"/>
    <text class="slide-title" x="9" y="17">3D DATA COLUMN CHART</text>
    <text class="slide-sub" x="9" y="23">Enter your subtitle here</text>
    <use href="#intro-copy" width="355" height="203"/>
    <g stroke="#ddd" stroke-width=".5" fill="none">
      <path d="M45 162 L255 162 L300 130 L300 60"/><path d="M45 162 L45 100 L90 70 L300 70"/>
    </g>
    <g>
      <rect x="128" y="92" width="14" height="40" fill="#888"/><polygon points="142,92 147,88 147,128 142,132" fill="#555"/>
      <rect x="162" y="98" width="14" height="34" fill="#888"/><polygon points="176,98 181,94 181,128 176,132" fill="#555"/>
      <rect x="196" y="82" width="14" height="50" fill="#888"/><polygon points="210,82 215,78 215,128 210,132" fill="#555"/>
      <rect x="236" y="75" width="14" height="57" fill="var(--red)"/><polygon points="236,75 241,71 255,71 250,75" fill="#f2545a"/><polygon points="250,75 255,71 255,128 250,132" fill="#9e1016"/>
      <rect x="108" y="108" width="14" height="34" fill="var(--red)"/><polygon points="122,108 127,104 127,138 122,142" fill="#9e1016"/>
      <rect x="145" y="112" width="14" height="30" fill="var(--red)"/><polygon points="159,112 164,108 164,138 159,142" fill="#9e1016"/>
      <rect x="182" y="100" width="14" height="42" fill="var(--red)"/><polygon points="196,100 201,96 201,138 196,142" fill="#9e1016"/>
      <rect x="218" y="96" width="14" height="46" fill="#777"/><polygon points="232,96 237,92 237,138 232,142" fill="#444"/>
      <rect x="72" y="120" width="16" height="40" fill="var(--red)"/><polygon points="88,120 93,116 93,156 88,160" fill="#9e1016"/>
      <rect x="112" y="134" width="16" height="26" fill="var(--red)"/><polygon points="128,134 133,130 133,156 128,160" fill="#9e1016"/>
      <rect x="152" y="126" width="16" height="34" fill="var(--red)"/><polygon points="168,126 173,122 173,156 168,160" fill="#9e1016"/>
      <rect x="192" y="116" width="16" height="44" fill="var(--red)"/><polygon points="208,116 213,112 213,156 208,160" fill="#9e1016"/>
    </g>
    <g class="axis">
      <text x="38" y="108">5</text><text x="38" y="119">4</text><text x="38" y="130">3</text><text x="38" y="141">2</text><text x="38" y="152">1</text><text x="38" y="163">0</text>
      <text x="70" y="172">Category 1</text><text x="110" y="172">Category 2</text><text x="150" y="172">Category 3</text><text x="190" y="172">Category 4</text>
      <text x="262" y="150">Series 1</text><text x="280" y="140">Series 2</text><text x="296" y="128">Series 3</text>
    </g>
  </svg>

  <!-- 8 Bar chart -->
  <svg class="slide" viewBox="0 0 355 203" preserveAspectRatio="none">
    <use href="#slide-chrome" width="355" height="203"/>
    <text class="slide-title" x="9" y="17">BAR CHART</text>
    <text class="slide-sub" x="9" y="23">Enter your subtitle here</text>
    <use href="#intro-copy" width="355" height="203"/>
    <g class="grid"><line x1="40" x2="40" y1="76" y2="165"/><line x1="60" x2="60" y1="76" y2="165"/><line x1="80" x2="80" y1="76" y2="165"/><line x1="100" x2="100" y1="76" y2="165"/><line x1="120" x2="120" y1="76" y2="165"/></g>
    <g>
      <rect x="40" y="82" width="60" height="4" fill="#000"/><rect x="40" y="87" width="35" height="4" fill="var(--grey)"/><rect x="40" y="92" width="70" height="4" fill="var(--red)"/>
      <rect x="40" y="110" width="48" height="4" fill="#000"/><rect x="40" y="115" width="88" height="4" fill="var(--grey)"/><rect x="40" y="120" width="56" height="4" fill="var(--red)"/>
      <rect x="40" y="138" width="44" height="4" fill="#000"/><rect x="40" y="143" width="62" height="4" fill="var(--grey)"/><rect x="40" y="148" width="126" height="4" fill="var(--red)"/>
    </g>
    <g class="axis" text-anchor="end"><text x="36" y="91">2002</text><text x="36" y="119">2005</text><text x="36" y="147">2018</text></g>
    <g class="axis" text-anchor="middle"><text x="40" y="172">0</text><text x="60" y="172">1</text><text x="80" y="172">2</text><text x="100" y="172">3</text><text x="120" y="172">4</text><text x="140" y="172">5</text></g>
    <text class="label" x="256" y="74" text-anchor="middle">Title Goes Here</text>
    <line x1="190" x2="322" y1="80" y2="80" stroke="#888" stroke-width=".6" stroke-dasharray="1.5 1.5"/>
    <text class="body-copy" x="190" y="89">Sample copy explains what the bars show.</text>
    <text class="body-copy" x="190" y="95">Compare each year and note the main trend</text>
    <text class="body-copy" x="190" y="101">before moving on to the next slide topic.</text>
    <circle cx="220" cy="133" r="8" fill="#333"/><circle cx="220" cy="133" r="3" fill="none" stroke="#fff" stroke-width=".9"/>
    <circle cx="262" cy="133" r="8" fill="#aaa"/><rect x="258" y="129" width="8" height="8" fill="none" stroke="#fff" stroke-width=".9"/>
    <circle cx="304" cy="133" r="8" fill="var(--red)"/><circle cx="304" cy="133" r="4" fill="none" stroke="#fff" stroke-width="1.2"/>
    <g text-anchor="middle">
      <text class="label" x="220" y="151">Your Title Here</text><text class="small" x="220" y="157">Short text line</text>
      <text class="label" x="262" y="151">Your Title Here</text><text class="small" x="262" y="157">Short text line</text>
      <text class="label" x="304" y="151">Your Title Here</text><text class="small" x="304" y="157">Short text line</text>
    </g>
  </svg>

  <!-- 9 Line chart -->
  <svg class="slide" viewBox="0 0 355 203" preserveAspectRatio="none">
    <use href="#slide-chrome" width="355" height="203"/>
    <text class="slide-title" x="9" y="17">LINE CHART</text>
    <text class="slide-sub" x="9" y="23">Enter your subtitle here</text>
    <use href="#intro-copy" width="355" height="203"/>
    <g class="grid"><line x1="40" x2="330" y1="64" y2="64"/><line x1="40" x2="330" y1="77" y2="77"/><line x1="40" x2="330" y1="90" y2="90"/><line x1="40" x2="330" y1="103" y2="103"/><line x1="40" x2="330" y1="116" y2="116"/><line x1="40" x2="330" y1="129" y2="129"/><line x1="40" x2="330" y1="142" y2="142"/></g>
    <g class="axis" text-anchor="end"><text x="34" y="65">6</text><text x="34" y="78">5</text><text x="34" y="91">4</text><text x="34" y="104">3</text><text x="34" y="117">2</text><text x="34" y="130">1</text><text x="34" y="143">0</text></g>
    <polyline points="72,90 144,112 216,100 288,82" fill="none" stroke="var(--red)" stroke-width="1"/>
    <polyline points="72,112 144,85 216,118 288,96" fill="none" stroke="#000" stroke-width="1"/>
    <polyline points="72,118 144,108 216,106 288,78" fill="none" stroke="#bbb" stroke-width="1"/>
    <g class="axis" text-anchor="middle"><text x="72" y="150">Category 1</text><text x="144" y="150">Category 2</text><text x="216" y="150">Category 3</text><text x="288" y="150">Category 4</text></g>
    <g>
      <circle cx="42" cy="167" r="1.6" fill="var(--red)"/><text class="label" x="48" y="166">Enter Your Title Here</text><text class="small" x="48" y="172">Short text line</text>
      <circle cx="142" cy="167" r="1.6" fill="#000"/><text class="label" x="148" y="166">Enter Your Title Here</text><text class="small" x="148" y="172">Short text line</text>
      <circle cx="232" cy="167" r="1.6" fill="#bbb"/><text class="label" x="238" y="166">Enter Your Title Here</text><text class="small" x="238" y="172">Short text line</text>
    </g>
  </svg>

  <!-- 10 Line chart style 1 -->
  <svg class="slide" viewBox="0 0 355 203" preserveAspectRatio="none">
    <use href="#slide-chrome" width="355" height="203"/>
    <text class="slide-title" x="9" y="17">LINE CHART STYLE - 1</text>
    <text class="slide-sub" x="9" y="23">Enter your subtitle here</text>
    <use href="#intro-copy" width="355" height="203"/>
    <g class="grid"><line x1="64" x2="300" y1="56" y2="56"/><line x1="64" x2="300" y1="76" y2="76"/><line x1="64" x2="300" y1="96" y2="96"/><line x1="64" x2="300" y1="116" y2="116"/><line x1="64" x2="300" y1="136" y2="136"/></g>
    <g class="axis" text-anchor="end"><text x="58" y="57">5</text><text x="58" y="67">4.5</text><text x="58" y="77">4</text><text x="58" y="87">3.5</text><text x="58" y="97">3</text><text x="58" y="107">2.5</text><text x="58" y="117">2</text><text x="58" y="127">1.5</text><text x="58" y="137">1</text></g>
    <path d="M75 64 C100 110, 120 140, 140 138 C170 132, 190 80, 220 72 C240 66, 255 64, 268 63" fill="none" stroke="#000" stroke-width="1"/>
    <path d="M75 96 C95 80, 115 60, 140 62 C170 66, 185 105, 205 120 C225 134, 250 132, 268 134" fill="none" stroke="var(--red)" stroke-width="1"/>
    <path d="M75 100 C100 100, 120 100, 140 100 C165 100, 180 86, 205 84 C230 88, 250 96, 268 90" fill="none" stroke="#8ab04a" stroke-width="1"/>
    <g fill="#fff" stroke-width=".8">
      <circle cx="75" cy="64" r="1.6" stroke="#000"/><circle cx="140" cy="62" r="1.6" stroke="var(--red)"/><circle cx="205" cy="84" r="1.6" stroke="#8ab04a"/>
      <circle cx="75" cy="96" r="1.6" stroke="var(--red)"/><circle cx="140" cy="138" r="1.6" stroke="#000"/><circle cx="268" cy="90" r="1.6" stroke="#8ab04a"/>
    </g>
    <g class="axis" text-anchor="middle"><text x="75" y="148">2014</text><text x="107" y="148">2016</text><text x="139" y="148">2018</text><text x="171" y="148">2020</text><text x="203" y="148">2022</text><text x="235" y="148">2024</text><text x="267" y="148">2026</text><text x="299" y="148">2028</text></g>
    <g class="label"><rect x="82" y="167" width="3" height="3" fill="#555" transform="rotate(45 83.5 168.5)"/><text x="89" y="170">Your Tittle</text>
      <rect x="160" y="167" width="3" height="3" fill="var(--red)" transform="rotate(45 161.5 168.5)"/><text x="167" y="170">Your Tittle</text>
      <rect x="238" y="167" width="3" height="3" fill="#000" transform="rotate(45 239.5 168.5)"/><text x="245" y="170">Your Tittle</text></g>
  </svg>

  <!-- 11 Line chart style 2 -->
  <svg class="slide" viewBox="0 0 355 203" preserveAspectRatio="none">
    <use href="#slide-chrome" width="355" height="203"/>
    <text class="slide-title" x="9" y="17">LINE CHART STYLE - 2</text>
    <text class="slide-sub" x="9" y="23">Enter your subtitle here</text>
    <use href="#intro-copy" width="355" height="203"/>
    <g class="grid"><line x1="64" x2="300" y1="56" y2="56"/><line x1="64" x2="300" y1="76" y2="76"/><line x1="64" x2="300" y1="96" y2="96"/><line x1="64" x2="300" y1="116" y2="116"/><line x1="64" x2="300" y1="136" y2="136"/></g>
    <g class="axis" text-anchor="end"><text x="58" y="57">5</text><text x="58" y="67">4.5</text><text x="58" y="77">4</text><text x="58" y="87">3.5</text><text x="58" y="97">3</text><text x="58" y="107">2.5</text><text x="58" y="117">2</text><text x="58" y="127">1.5</text><text x="58" y="137">1</text></g>
    <polyline points="75,64 140,136 205,86 268,60" fill="none" stroke="#777" stroke-width=".9"/>
    <polyline points="75,110 140,88 205,104 268,96" fill="none" stroke="#e97a7f" stroke-width=".9"/>
    <polyline points="75,122 140,120 205,78 268,120" fill="none" stroke="#aaa" stroke-width=".9"/>
    <g fill="#fff" stroke="#777" stroke-width=".7">
      <circle cx="75" cy="64" r="1.6"/><circle cx="140" cy="136" r="1.6"/><circle cx="205" cy="86" r="1.6"/><circle cx="268" cy="60" r="1.6"/>
      <circle cx="75" cy="110" r="1.6" stroke="#e97a7f"/><circle cx="205" cy="104" r="1.6" stroke="#e97a7f"/><circle cx="205" cy="78" r="1.6"/>
    </g>
    <g class="axis" text-anchor="middle"><text x="75" y="148">2014</text><text x="107" y="148">2016</text><text x="139" y="148">2018</text><text x="171" y="148">2020</text><text x="203" y="148">2022</text><text x="235" y="148">2024</text><text x="267" y="148">2026</text><text x="299" y="148">2028</text></g>
    <g class="label"><rect x="82" y="167" width="3" height="3" fill="#555" transform="rotate(45 83.5 168.5)"/><text x="89" y="170">Your Tittle</text>
      <rect x="160" y="167" width="3" height="3" fill="var(--red)" transform="rotate(45 161.5 168.5)"/><text x="167" y="170">Your Tittle</text>
      <rect x="238" y="167" width="3" height="3" fill="#aaa" transform="rotate(45 239.5 168.5)"/><text x="245" y="170">Your Tittle</text></g>
  </svg>

  <!-- 12 Pyramid style data chart -->
  <svg class="slide" viewBox="0 0 355 203" preserveAspectRatio="none">
    <use href="#slide-chrome" width="355" height="203"/>
    <text class="slide-title" x="9" y="17">PYRAMID STYLE DATA CHART</text>
    <text class="slide-sub" x="9" y="23">Enter your subtitle here</text>
    <use href="#intro-copy" width="355" height="203"/>
    <g stroke="#ddd" stroke-width=".5" fill="none"><path d="M60 150 L220 150 L265 118 L265 64"/><path d="M60 150 L60 100 L105 68 L265 68"/></g>
    <g>
      <polygon points="108,66 98,110 114,106" fill="#888"/><polygon points="108,66 114,106 120,104" fill="#555"/>
      <polygon points="140,74 130,104 146,102" fill="#999"/><polygon points="140,74 146,102 152,100" fill="#666"/>
      <polygon points="172,84 162,108 178,106" fill="#aaa"/><polygon points="172,84 178,106 184,104" fill="#666"/>
      <polygon points="204,88 196,110 210,108" fill="#aaa"/><polygon points="204,88 210,108 215,106" fill="#666"/>
      <polygon points="90,78 76,142 98,138" fill="#777"/><polygon points="90,78 98,138 106,134" fill="#3a3a3a"/>
      <polygon points="124,96 112,140 132,136" fill="#888"/><polygon points="124,96 132,136 138,134" fill="#444"/>
      <polygon points="158,94 146,138 166,134" fill="#888"/><polygon points="158,94 166,134 172,132" fill="#444"/>
      <polygon points="192,106 182,136 198,132" fill="#999"/><polygon points="192,106 198,132 204,130" fill="#555"/>
      <polygon points="226,116 218,134 232,130" fill="#aaa"/><polygon points="226,116 232,130 237,128" fill="#666"/>
    </g>
    <g class="axis"><text x="52" y="113">5</text><text x="52" y="124">3</text><text x="52" y="135">1</text>
      <text x="72" y="160">Title - 01</text><text x="106" y="160">Title - 02</text><text x="140" y="160">Title - 03</text><text x="174" y="160">Title - 04</text><text x="208" y="160">Title - 05</text>
      <text x="250" y="150">Revenue</text><text x="260" y="142">Sales 1</text><text x="270" y="134">Sales 2</text></g>
  </svg>

  <!-- 13 Gantt chart -->
  <svg class="slide" viewBox="0 0 355 203" preserveAspectRatio="none">
    <use href="#slide-chrome" width="355" height="203"/>
    <text class="slide-title" x="9" y="17">GANTT CHART</text>
    <text class="slide-sub" x="9" y="23">Enter your subtitle here</text>
    <g class="small">
      <text x="24" y="50">Activity - 01</text><text x="24" y="57">Activity - 02</text><text x="24" y="64">Activity - 03</text><text x="24" y="71">Activity - 04</text><text x="24" y="78">Activity - 05</text><text x="24" y="85">Activity - 06</text><text x="24" y="92">Activity - 07</text><text x="24" y="99">Activity - 08</text><text x="24" y="106">Activity - 09</text><text x="24" y="113">Activity - 10</text>
    </g>
    <g>
      <rect x="90" y="47" width="22" height="3" rx="1.5" fill="var(--red)"/>
      <rect x="104" y="54" width="24" height="3" rx="1.5" fill="var(--red)"/>
      <rect x="122" y="61" width="22" height="3" rx="1.5" fill="var(--red)"/>
      <rect x="138" y="68" width="30" height="3" rx="1.5" fill="var(--red)"/>
      <rect x="180" y="75" width="18" height="3" rx="1.5" fill="#222"/>
      <rect x="196" y="82" width="24" height="3" rx="1.5" fill="#888"/>
      <rect x="198" y="89" width="30" height="3" rx="1.5" fill="#888"/>
      <rect x="230" y="96" width="20" height="3" rx="1.5" fill="#888"/>
      <rect x="230" y="103" width="22" height="3" rx="1.5" fill="#888"/>
      <rect x="256" y="110" width="20" height="3" rx="1.5" fill="#bbb"/>
    </g>
    <g stroke="#999" stroke-width=".5">
      <line x1="220" y1="82" x2="220" y2="146"/><line x1="250" y1="96" x2="250" y2="146"/><line x1="282" y1="112" x2="282" y2="146"/>
    </g>
    <path d="M282 120 V112 L290 114 L282 116" fill="#f2c12e"/>
    <text class="small" x="296" y="122">Production</text>
    <g>
      <rect x="60" y="142" width="24" height="8" fill="var(--red)"/>
      <rect x="84" y="142" width="18" height="8" fill="#000"/><rect x="102" y="142" width="18" height="8" fill="#888"/>
      <rect x="120" y="142" width="18" height="8" fill="#000"/><rect x="138" y="142" width="18" height="8" fill="#888"/>
      <rect x="156" y="142" width="18" height="8" fill="var(--red)"/><rect x="174" y="142" width="18" height="8" fill="#000"/>
      <rect x="192" y="142" width="18" height="8" fill="var(--red)"/><rect x="210" y="142" width="18" height="8" fill="#000"/>
      <rect x="228" y="142" width="18" height="8" fill="#888"/><rect x="246" y="142" width="18" height="8" fill="#bbb"/>
      <rect x="264" y="142" width="18" height="8" fill="var(--red)"/><rect x="282" y="142" width="18" height="8" fill="#000"/>
    </g>
    <g text-anchor="middle" style="font-size:3.6px;fill:#fff">
      <text x="72" y="147.5">Day 1</text><text x="93" y="147.5">6</text><text x="111" y="147.5">11</text><text x="129" y="147.5">16</text><text x="147" y="147.5">21</text><text x="165" y="147.5">26</text><text x="183" y="147.5">31</text><text x="201" y="147.5">36</text><text x="219" y="147.5">41</text><text x="237" y="147.5">46</text><text x="255" y="147.5">51</text><text x="273" y="147.5">56</text>
    </g>
    <g fill="#222"><path d="M70 153 l3 -3 l3 3 Z"/><path d="M176 153 l3 -3 l3 3 Z"/><path d="M246 153 l3 -3 l3 3 Z"/><path d="M296 153 l3 -3 l3 3 Z"/></g>
    <g class="small" text-anchor="middle"><text x="73" y="159">Year Text - 01</text><text x="179" y="159">Year Text - 02</text><text x="249" y="159">Year Text - 03</text><text x="299" y="159">Year Text - 04</text></g>
  </svg>

  <!-- 14 Data chart style 1 -->
  <svg class="slide" viewBox="0 0 355 203" preserveAspectRatio="none">
    <use href="#slide-chrome" width="355" height="203"/>
    <text class="slide-title" x="9" y="17">DATA CHART STYLE - 1</text>
    <text class="slide-sub" x="9" y="23">Enter your subtitle here</text>
    <use href="#intro-copy" width="355" height="203"/>
    <g fill="none" stroke-width="6">
      <circle cx="60" cy="118" r="23" stroke="#ddd"/><circle cx="60" cy="118" r="23" stroke="#111" pathLength="100" stroke-dasharray="35 100" transform="rotate(-90 60 118)"/>
      <circle cx="145" cy="118" r="23" stroke="#ddd"/><circle cx="145" cy="118" r="23" stroke="var(--red)" pathLength="100" stroke-dasharray="80 100" transform="rotate(-90 145 118)"/>
      <circle cx="228" cy="118" r="23" stroke="#ddd"/><circle cx="228" cy="118" r="23" stroke="#111" pathLength="100" stroke-dasharray="50 100" transform="rotate(-90 228 118)"/>
      <circle cx="312" cy="118" r="23" stroke="#ddd"/><circle cx="312" cy="118" r="23" stroke="var(--red)" pathLength="100" stroke-dasharray="90 100" transform="rotate(-90 312 118)"/>
    </g>
    <g class="big-num" text-anchor="middle"><text x="60" y="121">35%</text><text x="145" y="121">80%</text><text x="228" y="121">50%</text><text x="312" y="121">90%</text></g>
    <g text-anchor="middle">
      <text class="label" x="60" y="157">Your Title Here</text><text class="small" x="60" y="163">Short text line here</text>
      <text class="label" x="145" y="157">Your Title Here</text><text class="small" x="145" y="163">Short text line here</text>
      <text class="label" x="228" y="157">Your Title Here</text><text class="small" x="228" y="163">Short text line here</text>
      <text class="label" x="312" y="157">Your Title Here</text><text class="small" x="312" y="163">Short text line here</text>
    </g>
  </svg>

  <!-- 15 Data chart style 2 -->
  <svg class="slide" viewBox="0 0 355 203" preserveAspectRatio="none">
    <use href="#slide-chrome" width="355" height="203"/>
    <text class="slide-title" x="9" y="17">DATA CHART STYLE - 2</text>
    <text class="slide-sub" x="9" y="23">Enter your subtitle here</text>
    <use href="#intro-copy" width="355" height="203"/>
    <g class="small">
      <rect x="118" y="62" width="3" height="3" fill="#ccc"/><text x="122" y="65">Debt</text>
      <rect x="138" y="62" width="3" height="3" fill="#999"/><text x="142" y="65">Asset</text>
      <rect x="160" y="62" width="3" height="3" fill="#555"/><text x="164" y="65">Equity</text>
      <rect x="184" y="62" width="3" height="3" fill="#000"/><text x="188" y="65">Cost</text>
      <rect x="204" y="62" width="3" height="3" fill="var(--red)"/><text x="208" y="65">Income</text>
    </g>
    <g>
      <rect x="30" y="124" width="8" height="26" fill="#ccc"/><rect x="40" y="98" width="8" height="52" fill="#999"/><rect x="50" y="122" width="8" height="28" fill="#555"/><rect x="60" y="103" width="8" height="47" fill="#000"/><rect x="70" y="108" width="8" height="42" fill="var(--red)"/>
      <rect x="106" y="122" width="8" height="28" fill="#ccc"/><rect x="116" y="108" width="8" height="42" fill="#999"/><rect x="126" y="98" width="8" height="52" fill="#555"/><rect x="136" y="108" width="8" height="42" fill="#000"/><rect x="146" y="103" width="8" height="47" fill="var(--red)"/>
      <rect x="184" y="103" width="8" height="47" fill="#ccc"/><rect x="194" y="118" width="8" height="32" fill="#999"/><rect x="204" y="80" width="8" height="70" fill="#555"/><rect x="214" y="86" width="8" height="64" fill="#000"/><rect x="224" y="98" width="8" height="52" fill="var(--red)"/>
      <rect x="262" y="108" width="8" height="42" fill="#ccc"/><rect x="272" y="124" width="8" height="26" fill="#999"/><rect x="282" y="103" width="8" height="47" fill="#555"/><rect x="292" y="98" width="8" height="52" fill="#000"/><rect x="302" y="86" width="8" height="64" fill="var(--red)"/>
    </g>
    <g text-anchor="middle">
      <text class="label" x="54" y="162">Your Title Here</text><text class="small" x="54" y="168">Short text line here</text>
      <text class="label" x="130" y="162">Your Title Here</text><text class="small" x="130" y="168">Short text line here</text>
      <text class="label" x="208" y="162">Your Title Here</text><text class="small" x="208" y="168">Short text line here</text>
      <text class="label" x="286" y="162">Your Title Here</text><text class="small" x="286" y="168">Short text line here</text>
    </g>
  </svg>

  <!-- 16 Data display style (bars) -->
  <svg class="slide" viewBox="0 0 355 203" preserveAspectRatio="none">
    <use href="#slide-chrome" width="355" height="203"/>
    <text class="slide-title" x="9" y="17">DATA DISPLAY STYLE</text>
    <text class="slide-sub" x="9" y="23">Enter your subtitle here</text>
    <use href="#intro-copy" width="355" height="203"/>
    <g>
      <rect x="36" y="60" width="60" height="4" fill="#000"/><rect x="36" y="66" width="30" height="3" fill="var(--red)"/>
      <rect x="36" y="80" width="70" height="4" fill="#000"/><rect x="36" y="86" width="40" height="3" fill="var(--red)"/>
      <rect x="36" y="100" width="70" height="4" fill="#000"/><rect x="36" y="106" width="60" height="3" fill="var(--red)"/>
      <rect x="36" y="120" width="30" height="4" fill="#000"/><rect x="36" y="126" width="60" height="3" fill="var(--red)"/>
      <rect x="198" y="60" width="18" height="4" fill="#000"/><rect x="198" y="66" width="30" height="3" fill="var(--red)"/>
      <rect x="198" y="80" width="60" height="4" fill="#000"/><rect x="198" y="86" width="50" height="3" fill="var(--red)"/>
      <rect x="198" y="100" width="40" height="4" fill="#000"/><rect x="198" y="106" width="50" height="3" fill="var(--red)"/>
      <rect x="198" y="120" width="40" height="4" fill="#000"/><rect x="198" y="126" width="60" height="3" fill="var(--red)"/>
    </g>
    <g class="axis" text-anchor="end"><text x="32" y="66">2014</text><text x="32" y="86">2013</text><text x="32" y="106">2012</text><text x="32" y="126">2011</text>
      <text x="194" y="66">2014</text><text x="194" y="86">2013</text><text x="194" y="106">2012</text><text x="194" y="126">2011</text></g>
    <g>
      <text class="label" x="122" y="66">Title - 01</text><text class="small" x="122" y="72">Short text line</text>
      <text class="label" x="122" y="106">Title - 02</text><text class="small" x="122" y="112">Short text line</text>
      <text class="label" x="284" y="66" style="fill:#111">Title - 03</text><text class="small" x="284" y="72">Short text line</text>
      <text class="label" x="284" y="106" style="fill:var(--red)">Title - 04</text><text class="small" x="284" y="112">Short text line</text>
    </g>
    <rect x="22" y="142" width="150" height="40" fill="var(--red)"/>
    <text x="30" y="174" style="font-size:24px;fill:#fff">34%</text>
    <text x="90" y="158" style="font-size:4px;fill:#fff;font-weight:600">Second Opinion</text>
    <text x="90" y="164" style="font-size:3px;fill:#fde">Short supporting text</text>
    <rect x="184" y="142" width="150" height="40" fill="var(--red)"/>
    <text x="192" y="174" style="font-size:24px;fill:#fff">12%</text>
    <text x="252" y="158" style="font-size:4px;fill:#fff;font-weight:600">Wall Block</text>
    <text x="252" y="164" style="font-size:3px;fill:#fde">Short supporting text</text>
  </svg>

  <!-- 17 Data display style (arcs) -->
  <svg class="slide" viewBox="0 0 355 203" preserveAspectRatio="none">
    <use href="#slide-chrome" width="355" height="203"/>
    <text class="slide-title" x="9" y="17">DATA DISPLAY STYLE</text>
    <text class="slide-sub" x="9" y="23">Enter your subtitle here</text>
    <use href="#intro-copy" width="355" height="203"/>
    <g fill="none" stroke-width="6">
      <circle cx="92" cy="132" r="44" stroke="var(--red)" pathLength="100" stroke-dasharray="58 100" transform="rotate(-90 92 132)"/>
      <circle cx="92" cy="132" r="35" stroke="#000" pathLength="100" stroke-dasharray="65 100" transform="rotate(-120 92 132)"/>
      <circle cx="92" cy="132" r="26" stroke="var(--red)" pathLength="100" stroke-dasharray="71 100" transform="rotate(-150 92 132)"/>
      <circle cx="92" cy="132" r="17" stroke="#000" pathLength="100" stroke-dasharray="77 100" transform="rotate(-180 92 132)"/>
    </g>
    <g stroke="#bbb" stroke-width=".5"><line x1="92" y1="84" x2="168" y2="84"/><line x1="92" y1="97" x2="168" y2="97"/><line x1="92" y1="106" x2="168" y2="106"/><line x1="92" y1="115" x2="168" y2="115"/></g>
    <g class="small"><text x="156" y="82">58%</text><text x="156" y="95">65%</text><text x="156" y="104">71%</text><text x="156" y="113">77%</text></g>
    <g class="small">
      <circle cx="174" cy="84" r="1.3" fill="#000"/><text x="178" y="85">Short note about this value</text>
      <circle cx="174" cy="97" r="1.3" fill="#000"/><text x="178" y="98">Short note about this value</text>
      <circle cx="174" cy="106" r="1.3" fill="#000"/><text x="178" y="107">Short note about this value</text>
      <circle cx="174" cy="115" r="1.3" fill="#000"/><text x="178" y="116">Short note about this value</text>
    </g>
    <g>
      <circle cx="178" cy="140" r="2.4" fill="var(--red)"/><text class="label" x="184" y="138">Enter Your Title Here</text><text class="small" x="184" y="144">Short text line</text>
      <circle cx="258" cy="140" r="2.4" fill="#000"/><text class="label" x="264" y="138">Enter Your Title Here</text><text class="small" x="264" y="144">Short text line</text>
      <circle cx="178" cy="164" r="2.4" fill="#000"/><text class="label" x="184" y="162">Enter Your Title Here</text><text class="small" x="184" y="168">Short text line</text>
      <circle cx="258" cy="164" r="2.4" fill="var(--red)"/><text class="label" x="264" y="162">Enter Your Title Here</text><text class="small" x="264" y="168">Short text line</text>
    </g>
  </svg>

  <!-- 18 Chart style 1 -->
  <svg class="slide" viewBox="0 0 355 203" preserveAspectRatio="none">
    <use href="#slide-chrome" width="355" height="203"/>
    <text class="slide-title" x="9" y="17">CHART STYLE - 1</text>
    <text class="slide-sub" x="9" y="23">Enter your subtitle here</text>
    <use href="#intro-copy" width="355" height="203"/>
    <g class="grid"><line x1="40" x2="200" y1="74" y2="74"/><line x1="40" x2="200" y1="92" y2="92"/><line x1="40" x2="200" y1="110" y2="110"/><line x1="40" x2="200" y1="128" y2="128"/><line x1="40" x2="200" y1="146" y2="146"/><line x1="40" x2="200" y1="164" y2="164"/></g>
    <g class="axis" text-anchor="end"><text x="34" y="75">50</text><text x="34" y="93">40</text><text x="34" y="111">30</text><text x="34" y="129">20</text><text x="34" y="147">10</text><text x="34" y="165">0</text></g>
    <g>
      <polygon points="50,164 80,92 110,164" fill="#555" opacity=".85"/>
      <polygon points="80,164 112,80 144,164" fill="#222" opacity=".9"/>
      <polygon points="112,164 140,110 168,164" fill="#888" opacity=".85"/>
      <polygon points="130,164 158,96 186,164" fill="var(--red)" opacity=".8"/>
      <polygon points="150,164 172,120 194,164" fill="#f07a80" opacity=".8"/>
    </g>
    <g class="axis" text-anchor="middle"><text x="50" y="171">1</text><text x="66" y="171">2</text><text x="82" y="171">3</text><text x="98" y="171">4</text><text x="114" y="171">5</text><text x="130" y="171">6</text><text x="146" y="171">7</text><text x="162" y="171">8</text><text x="178" y="171">9</text><text x="194" y="171">10</text></g>
    <g class="label">
      <rect x="30" y="180" width="3" height="3" fill="#000" transform="rotate(45 31.5 181.5)"/><text x="37" y="183">Your Tittle</text>
      <rect x="90" y="180" width="3" height="3" fill="#777" transform="rotate(45 91.5 181.5)"/><text x="97" y="183">Your Tittle</text>
      <rect x="150" y="180" width="3" height="3" fill="var(--red)" transform="rotate(45 151.5 181.5)"/><text x="157" y="183">Your Tittle</text>
    </g>
    <text class="label" x="268" y="78" text-anchor="middle">Title Goes Here</text>
    <g class="body-copy" text-anchor="middle">
      <text x="268" y="90">Sample copy explains what the chart</text>
      <text x="268" y="96">shows and which value stands out most</text>
      <text x="268" y="102">across the ten periods on the left.</text>
      <text x="268" y="108">Keep the message short and clear so</text>
      <text x="268" y="114">the audience reads it in a glance.</text>
      <text x="268" y="124">Add one more line of context here</text>
      <text x="268" y="130">to support the final recommendation.</text>
    </g>
  </svg>

</main>
</body>
</html>
```